letter flyer KORVEN

please see our website www.tallowcrestpartners.com.au for details. however, we are a financial services company that has services in accounting and taxation, wealth advice, loan broking, general insurance and business advice. we want to target local potential business clients to focus on helping them conduct a review and work out what they need to do to improve the health and profitability of their business. we would like to create a letter/flyer to send them. we want the message to be as follows:
1) by having a review, we guarantee we will provide some financial benefit;
2) we are offering a cohesive and comprehensive team who will provide many financial services under one roof; and
3) we specialise in business.

we have called the campaign 'KORVEN'

we have drafted a letter as a concept and we need design, any suggested changes in wording and imagery to demonstrate our message. We do have a logo for each of the divisions above. we thought the reverse side could just be our logo and catchphrase 'financial freedom is...'

***** we just want an A4 letter... not a bifold flyer
***** I have also included a copy of our newsletter so you can get the logos and feel for our business

```html
<!DOCTYPE html>
<html lang="en">
<head>
<meta charset="utf-8">
<title>Tallowcrest Partners – KORVEN Business Check</title>
<link href="https://fonts.googleapis.com/css2?family=Lato:wght@400;700;900&family=Oswald:wght@500;600&family=Roboto+Condensed:wght@700&family=Michroma&display=swap" rel="stylesheet">
<style>
:root{
  --blue:#1d8be0;
  --blue-deep:#0f6fc4;
  --blue-light:#3aa6f0;
  --charcoal:#2b2b2e;
  --charcoal-2:#3c3c40;
  --ink:#2a2a2a;
  --text:#3a3a3a;
  --white:#ffffff;
  --page-bg:#e9e9ea;
  --gold:#c98a2b;
}
*{margin:0;padding:0;box-sizing:border-box}
html,body{width:806px;height:1200px;overflow:hidden;background:var(--page-bg)}
.flyer{
  position:absolute;left:0;top:34px;width:637px;height:895px;
  transform:scale(1.2653);transform-origin:0 0;
  background:var(--white);overflow:hidden;font-family:'Lato',sans-serif;color:var(--text);
}
.flyer-shapes{position:absolute;inset:0}
.abs{position:absolute}
.brand{left:22px;top:30px;display:flex;align-items:center;gap:10px}
.brand-dot{width:50px;height:50px;border-radius:50%;background:var(--blue-deep)}
.brand-name{font-family:'Lato',sans-serif;font-weight:700;font-size:15px;line-height:1.1;color:var(--charcoal);width:110px}
.brand-tagline{left:46px;top:94px;font-family:'Lato',sans-serif;font-weight:700;font-size:9.5px;color:var(--gold);letter-spacing:.3px}
.header-rule{left:201px;top:14px;width:1px;height:80px;background:#d4d4d4}
.call-out{left:216px;top:29px}
.call-out .lead{font-family:'Lato',sans-serif;font-weight:700;font-size:15px;color:var(--blue)}
.call-out .quote{font-family:'Lato',sans-serif;font-weight:400;font-size:19px;color:var(--ink);margin-top:1px}
.hero-title{left:15px;top:144px;font-family:'Oswald',sans-serif;font-weight:600;font-size:38px;color:var(--blue-light);letter-spacing:.2px;line-height:1}
.hero-sub{left:15px;font-family:'Roboto Condensed',sans-serif;font-weight:700;font-size:14.5px;letter-spacing:.2px}
.hero-sub.white{top:197px;color:var(--white)}
.hero-sub.blue{top:224px;color:var(--blue-light)}
.question{left:26px;display:flex;align-items:center;gap:14px;color:var(--white);font-weight:700;font-size:12px;line-height:1.3;width:240px}
.question .q-icon{flex:none;width:22px;height:22px;border-radius:50%;background:var(--blue);border:2px solid #e8f3fc;display:flex;align-items:center;justify-content:center}
.section-tab{left:0;height:24px;padding:0 22px 0 15px;background:var(--blue);color:var(--white);font-family:'Roboto Condensed',sans-serif;font-weight:700;font-size:15px;line-height:24px;border-radius:0 14px 14px 0}
.about-copy{left:16px;top:506px;width:346px;font-size:11.2px;line-height:1.31;text-align:justify;color:var(--text)}
.special-list{left:16px;top:670px;width:340px;list-style:none}
.special-list li{position:relative;padding-left:14px;font-weight:700;font-size:11.4px;line-height:1.6;color:var(--ink)}
.special-list li::before{content:"";position:absolute;left:0;top:7px;width:5px;height:5px;border-radius:50%;background:var(--blue)}
.special-list .indent{display:block}
.advantage-title{left:15px;top:780px;font-family:'Michroma',sans-serif;font-size:15.5px;color:var(--blue);letter-spacing:.5px}
.advantage-sub{left:15px;top:803px;font-family:'Roboto Condensed',sans-serif;font-weight:700;font-size:11.5px;color:var(--charcoal-2);letter-spacing:.3px}
.footer-contact{color:var(--white);font-size:11px;font-weight:700;display:flex;align-items:center;gap:5px}
.meaning-title{left:430px;top:572px;font-family:'Oswald',sans-serif;font-weight:500;font-size:24px;color:var(--charcoal);line-height:1}
.meaning-sub{left:430px;top:601px;font-family:'Lato',sans-serif;font-weight:900;font-size:19px;color:var(--white);line-height:1}
.meaning-rule{left:413px;top:632px;width:196px;height:1.5px;background:var(--white)}
.meaning-list{left:430px;top:644px;width:175px;list-style:none}
.meaning-list li{position:relative;padding-left:11px;color:var(--white);font-weight:700;font-size:11.3px;line-height:1.33;text-align:justify;margin-bottom:20px}
.meaning-list li::before{content:"";position:absolute;left:0;top:5px;width:5px;height:5px;border-radius:50%;background:var(--white)}
</style>
</head>
<body>
<div class="flyer">
  <svg class="flyer-shapes" width="637" height="895" viewBox="0 0 637 895" aria-hidden="false">
    <defs>
      <linearGradient id="panelBlue" x1="0" y1="0" x2="1" y2="1">
        <stop offset="0" stop-color="#3aa6f0"/>
        <stop offset="1" stop-color="#0f6fc4"/>
      </linearGradient>
      <linearGradient id="darkPanel" x1="0" y1="0" x2="1" y2="0">
        <stop offset="0" stop-color="#2b2b2e"/>
        <stop offset="1" stop-color="#3c3c40"/>
      </linearGradient>
      <radialGradient id="photoTone" cx="0.45" cy="0.5" r="0.6">
        <stop offset="0" stop-color="#f4f4f2"/>
        <stop offset="0.55" stop-color="#d9d6d0"/>
        <stop offset="1" stop-color="#3a3d44"/>
      </radialGradient>
    </defs>
    <!-- blue outline band around hero panel -->
    <path d="M0,121 H336 Q346,121 354,129 L400,175" fill="none" stroke="#1d8be0" stroke-width="5"/>
    <!-- dark hero panel -->
    <path d="M0,130 H330 Q340,130 348,138 L392,182 V392 L350,432 H0 Z" fill="url(#darkPanel)"/>
    <path d="M0,438 H353 L398,395" fill="none" stroke="#1d8be0" stroke-width="4"/>
    <!-- right blue panel -->
    <path d="M398,400 V822 L471,895 H637 V400 Z" fill="url(#panelBlue)"/>
    <path d="M389,400 V826 L458,895" fill="none" stroke="#2b2b2e" stroke-width="7"/>
    <!-- circle rings and photo area -->
    <path d="M326,190 A205,205 0 0 1 637,140" fill="none" stroke="#2b2b2e" stroke-width="14"/>
    <circle cx="508" cy="300" r="192" fill="#ffffff"/>
    <circle cx="508" cy="300" r="188" fill="none" stroke="#1d8be0" stroke-width="8"/>
    <g role="img" aria-label="Photo of a hand in a business shirt drawing a rising arrow over a bar chart">
      <circle cx="508" cy="300" r="178" fill="url(#photoTone)"/>
    </g>
    <!-- footer bar -->
    <path d="M0,848 H440 L487,895 H0 Z" fill="#2b2b2e"/>
    <path d="M248,895 L263,880 H300 L285,895 Z" fill="#1d8be0"/>
    <path d="M300,895 L315,880 H350 L335,895 Z" fill="#ffffff"/>
    <path d="M350,895 L365,880 H400 L385,895 Z" fill="#1d8be0"/>
    <!-- footer icons -->
    <path d="M20,856 q-3,3 1,8 q5,6 9,4 l-2,-3 l-2,1 q-3,-2 -4,-5 l1,-2 z" fill="#1d8be0"/>
    <rect x="21" y="876" width="8" height="6" fill="#1d8be0"/>
    <circle cx="190" cy="860" r="4.5" fill="none" stroke="#1d8be0" stroke-width="1.5"/>
  </svg>

  <div class="abs brand"><span class="brand-dot"></span><span class="brand-name">Tallowcrest Partners</span></div>
  <div class="abs brand-tagline">YOUR WEALTH ADVISORS</div>
  <div class="abs header-rule"></div>
  <div class="abs call-out">
    <div class="lead">Simply call or email us</div>
    <div class="quote">And quote ‘KORVEN’</div>
  </div>

  <div class="abs hero-title">ARE YOU WORKING</div>
  <div class="abs hero-sub white">LONG HOURS AND FEEL LIKE YOU ARE NOT</div>
  <div class="abs hero-sub blue">REAPING THE BENEFITS YOU SHOULD BE?</div>

  <div class="abs question" style="top:276px"><span class="q-icon"><svg width="10" height="9" viewBox="0 0 10 9"><rect x="0" y="2" width="10" height="7" rx="1" fill="#fff"/><rect x="3" y="0" width="4" height="3" fill="none" stroke="#fff"/></svg></span>Do you have work life balance?</div>
  <div class="abs question" style="top:325px"><span class="q-icon"><svg width="8" height="11" viewBox="0 0 8 11"><path d="M4,0 L6,3 L5,11 H3 L2,3 Z" fill="#fff"/></svg></span>Do you understand your business-<br>es strengths and weaknesses?</div>
  <div class="abs question" style="top:378px"><span class="q-icon"><svg width="11" height="9" viewBox="0 0 11 9"><path d="M0,9 H11 M2,9 V5 M5,9 V3 M8,9 V1" stroke="#fff" stroke-width="1.6"/></svg></span>Do you feel like you have potential<br>to grow?</div>

  <div class="abs section-tab" style="top:466px">ABOUT US</div>
  <p class="abs about-copy">Our business is to help you better understand your business and help you to prepare unique strategies to improve the success and value of your business. We can assist to streamline your financial service relationships, providing all financial services under one roof. Such as, accounting and taxation, business planning, wealth planning, smsf, insurance, loan broking, general insurance and business planning.</p>

  <div class="abs section-tab" style="top:627px">SPECIALISED IN</div>
  <ul class="abs special-list">
    <li>By having a review, we guarantee<span class="indent">we will provide some financial benefit</span></li>
    <li>We are offering a cohesive and comprehensive team<span class="indent">who will provide many financial services under one roof</span></li>
    <li>We specialise in business</li>
  </ul>

  <div class="abs advantage-title">HOW TO TAKE ADVANTAGE</div>
  <div class="abs advantage-sub">OF YOUR INITIAL COMPLIMENTARY BUSINESS CHECK</div>

  <div class="abs footer-contact" style="left:33px;top:853px">1300 555 018</div>
  <div class="abs footer-contact" style="left:200px;top:853px">info@tallowcrestpartners.com.au</div>
  <div class="abs footer-contact" style="left:33px;top:871px">www.tallowcrestpartners.com.au</div>

  <div class="abs meaning-title">What does this</div>
  <div class="abs meaning-sub">mean for you?</div>
  <div class="abs meaning-rule"></div>
  <ul class="abs meaning-list">
    <li>Coordinated approach and one simple phone call to meet your financial requirements. This saves you time and effort</li>
    <li>A financial services team working together for your business review will ensure you have savings and maximise your financial position with a solid team behind you, all coordinated and on the same team</li>
  </ul>
</div>
</body>
</html>
```